Web Design Project - Shipping Industry

Goals and Objectives
The objective of the new website is to create a more modern look and feel. The site will also allow for a more effective means of communicating with members while providing the public with information and developments in the local, regional and international shipping industry.
Scope
The website will highlight the history of the organisation inclusive of text and photographs. It will take visitors through the years from beginning to present. Information on the history of the shipping industry will also be included.
It will feature current articles on the organisation, its members and stakeholders in the shipping industry. Member information as well as pertinent details regarding the organisation’s subsidiaries will be documented for the website.
Information as it relates to shipping statistics, case studies, laws and regulations, international treaties and trade documents, shipping terms, careers in shipping, job opportunities, training opportunities, information for shippers including port listing and trade lanes will be main features of the content for the website.
The Association’s community involvement, industry calendar events and related links relevant industry members will also be featured.
Target Market
• The General Public;
• Members of the organization;
• Shipping Industry Stakeholders (local, regional and international);
• Tertiary students conducting research.
• Potential employees
• Potential Business Partners
Best Practice Bench Marketing
The following websites are being looked at:
• Korvel Quayworks - http://www.korvelquayworks.example/ (preferred look)
• Tessaly Maritime Association - http://www.tma-freight.example/ (like image transition on main page)
• Drovna - http://www.drovna.example (professional look)
• PLW - http://www.pelworth.example (preferred color: blue in logo)
• Quillo - http://www.quillo.example/electronics/tv-video-audio/ (preferred look for links page: image + short text below + visit site link)
Expected Result
• 3 - 5 pages which must include: [1] main page [2] standard page [3] links page

```html
<!DOCTYPE html>
<html lang="en">
<head>
<meta charset="utf-8">
<title>Halvern Marine – Home</title>
<link href="https://fonts.googleapis.com/css2?family=Arimo:wght@400;700&display=swap" rel="stylesheet">
<style>
  :root {
    --navy: #00005e;
    --navy-deep: #000040;
    --navy-bright: #000c8a;
    --grey-band: #e9e9e9;
    --grey-hero: #c6c6c6;
    --grey-heading: #b4b4b4;
    --grey-sub: #8a8a8a;
    --text-dark: #222222;
    --text-list: #555555;
    --white: #ffffff;
    --nav-text: #e4e6f5;
  }
  * { box-sizing: border-box; margin: 0; padding: 0; }
  html, body { width: 1069px; height: 1200px; overflow: hidden; background: var(--white); }
  body { position: relative; font-family: "Arimo", Arial, sans-serif; color: var(--text-dark); }

  /* Header */
  .site-header {
    position: absolute; left: 0; top: 0; width: 1069px; height: 127px;
    background: linear-gradient(180deg, var(--navy-bright) 0%, var(--navy) 55%, var(--navy-deep) 100%);
  }
  .brand {
    position: absolute; left: 28px; top: 36px;
    font-family: "Arimo", Arial, sans-serif; font-size: 27px; font-weight: 400;
    letter-spacing: 1px; color: var(--nav-text); white-space: nowrap;
  }
  .search {
    position: absolute; left: 739px; top: 33px; width: 307px; height: 29px;
    background: var(--white); border-radius: 4px;
  }
  .search svg { position: absolute; right: 6px; top: 5px; }
  .main-nav {
    position: absolute; left: 228px; top: 88px; width: 818px; height: 39px;
    background: var(--navy); display: flex; justify-content: space-between; padding-right: 14px;
  }
  .main-nav a {
    display: block; height: 39px; line-height: 40px; white-space: nowrap; flex: none;
    color: var(--nav-text); text-decoration: none; font-size: 14px; letter-spacing: 0.5px;
  }
  .main-nav a.is-current {
    width: 95px; text-align: center;
    background: linear-gradient(180deg, #f2f2f2 0%, #c9c9c9 100%); color: var(--navy);
  }

  /* Hero */
  .hero { position: absolute; left: 0; top: 127px; width: 1069px; height: 362px; background: var(--grey-hero); }
  .hero-image {
    position: absolute; left: 24px; top: 14px; width: 1022px; height: 333px;
    border: 1px solid #e8eef5;
    background: linear-gradient(180deg, #f4f7fb 0%, #dfe7f1 40%, #a9bbd6 62%, #6c86b6 100%);
  }

  /* Feature cards */
  .card { position: absolute; top: 505px; width: 310px; }
  .card-media { height: 165px; background: var(--navy); padding: 9px; }
  .card-media div { width: 100%; height: 100%; }
  .media-vessel { background: linear-gradient(160deg, #1d6b77 0%, #2f8a8c 55%, #dfe8e6 100%); }
  .media-port { background: linear-gradient(180deg, #30406e 0%, #d58a4a 48%, #1d2236 60%, #c0a040 100%); }
  .card-body { height: 162px; background: var(--grey-band); border-bottom: 2px solid var(--navy); padding: 14px 22px 0 11px; }
  .card-title { font-size: 25px; font-weight: 700; color: var(--navy); line-height: 26px; letter-spacing: 0.3px; }
  .card-subtitle { font-size: 21px; color: var(--grey-sub); line-height: 22px; letter-spacing: 0.5px; margin-bottom: 6px; }
  .card-text { font-size: 14px; line-height: 19px; padding-left: 2px; }
  .read-more {
    position: absolute; right: 5px; top: 329px; width: 87px; height: 28px;
    background: var(--navy); color: #dde0ef; font-size: 10.5px; letter-spacing: 0.8px;
    text-align: center; line-height: 28px; text-decoration: none;
  }
  .card-performance { left: 23px; }
  .card-about { left: 378px; }
  .card-services { left: 736px; }
  .services-panel { height: 327px; background: var(--grey-band); padding: 14px 19px 0; }
  .services-panel h2 { font-size: 25px; font-weight: 700; color: var(--navy); letter-spacing: 0.3px; line-height: 26px; }
  .services-panel h2 span { font-weight: 400; color: var(--grey-sub); font-size: 21px; }
  .services-intro { font-size: 14px; line-height: 19px; padding-left: 11px; margin: 8px 0 5px; }

  .link-list { list-style: none; }
  .link-list li { font-size: 13.5px; color: var(--text-list); line-height: 25px; white-space: nowrap; }
  .services-panel .link-list li { padding-left: 11px; position: relative; }
  .services-panel .link-list li::before {
    content: ""; position: absolute; left: 0; top: 9px;
    border-left: 4px solid #b8b8b8; border-top: 3.5px solid transparent; border-bottom: 3.5px solid transparent;
  }

  /* Info band */
  .info-band { position: absolute; left: 0; top: 893px; width: 1069px; height: 240px; background: var(--grey-band); }
  .info-col { position: absolute; top: 20px; }
  .info-col h3 { font-size: 24px; font-weight: 700; color: var(--grey-heading); letter-spacing: 0.4px; margin-bottom: 24px; white-space: nowrap; }
  .info-col .link-list li { line-height: 25px; }
  .info-information { left: 34px; }
  .info-why { left: 390px; }
  .info-locations { left: 753px; }
  .map-area {
    position: absolute; left: -10px; top: 80px; width: 282px; height: 130px;
    background: radial-gradient(ellipse at center, #9e9e9e 0%, #b3b3b3 55%, rgba(233,233,233,0) 75%);
  }

  /* Footer */
  .site-footer {
    position: absolute; left: 0; top: 1133px; width: 1069px; height: 67px;
    background: var(--navy-deep); color: #d7d9ea; font-size: 11px; text-align: center; line-height: 67px; letter-spacing: 0.3px;
  }
</style>
</head>
<body>
  <header class="site-header">
    <div class="brand">HALVERN MARINE</div>
    <div class="search" role="search">
      <svg width="19" height="19" viewBox="0 0 19 19" aria-hidden="true">
        <circle cx="9.5" cy="9.5" r="9" fill="#b0b0b0"/>
        <circle cx="8.6" cy="8.6" r="3.6" fill="none" stroke="#fff" stroke-width="1.6"/>
        <line x1="11.3" y1="11.3" x2="14" y2="14" stroke="#fff" stroke-width="2" stroke-linecap="round"/>
      </svg>
    </div>
    <nav class="main-nav">
      <a class="is-current" href="#">HOME</a>
      <a href="#">ABOUT US</a>
      <a href="#">CAPABILITIES</a>
      <a href="#">NEWS</a>
      <a href="#">SERVICES</a>
      <a href="#">CAREERS</a>
      <a href="#">CONTACT US</a>
    </nav>
  </header>

  <section class="hero">
    <div class="hero-image" role="img" aria-label="Container ship sailing on calm water under a pale sky"></div>
  </section>

  <article class="card card-performance">
    <div class="card-media"><div class="media-vessel" role="img" aria-label="Loaded container vessel under way at sea"></div></div>
    <div class="card-body">
      <h2 class="card-title">PERFORMANCE</h2>
      <div class="card-subtitle">REDEFINED</div>
      <p class="card-text">Lorem ipsum dolor sit amet conse ctetur adipi sicing elit, sed do eiusmod tempor incididunt ut labore et dolore magna aliqua.</p>
    </div>
    <a class="read-more" href="#">READ MORE</a>
  </article>

  <article class="card card-about">
    <div class="card-media"><div class="media-port" role="img" aria-label="Container port cranes lit at dusk reflected in the harbour"></div></div>
    <div class="card-body">
      <h2 class="card-title">ABOUT</h2>
      <div class="card-subtitle">OUR COMPANY</div>
      <p class="card-text">Lorem ipsum dolor sit amet conse ctetur adipi sicing elit, sed do eiusmod tempor incididunt ut labore et dolore magna aliqua.</p>
    </div>
    <a class="read-more" href="#">READ MORE</a>
  </article>

  <article class="card card-services">
    <div class="services-panel">
      <h2>OUR <span>SERVICES</span></h2>
      <p class="services-intro">Lorem ipsum dolor sit amet conse ctetur adipi sicing elit, sed do eiusmod</p>
      <ul class="link-list">
        <li>Lorem ipsum dolor sit amet conse</li>
        <li>Adipisicing elit, sed do eiusmod</li>
        <li>Tempor incididunt ut labore et dolore</li>
        <li>Aliqua enim ad minim</li>
        <li>Veniam, quis nostrud exercitation</li>
        <li>Ipsum dolor sit amet conse</li>
        <li>Adipisicing elit, sed do eiusmod</li>
        <li>Incididunt ut labore et dolore</li>
        <li>Magna aliqua enim ad minim</li>
      </ul>
    </div>
    <a class="read-more" href="#">READ MORE</a>
  </article>

  <section class="info-band">
    <div class="info-col info-information">
      <h3>INFORMATION</h3>
      <ul class="link-list">
        <li>Lorem ipsum dolor sit amet conse</li>
        <li>Adipisicing elit, sed do eiusmod</li>
        <li>Tempor incididunt ut labore et dolore</li>
        <li>Aliqua enim ad minim</li>
        <li>Veniam, quis nostrud exercitation</li>
        <li>Ipsum dolor sit amet conse</li>
      </ul>
    </div>
    <div class="info-col info-why">
      <h3>WHY BUY FROM US</h3>
      <ul class="link-list">
        <li>Lorem ipsum dolor sit amet conse</li>
        <li>Adipisicing elit, sed do eiusmod</li>
        <li>Tempor incididunt ut labore et dolore</li>
        <li>Aliqua enim ad minim</li>
        <li>Veniam, quis nostrud exercitation</li>
        <li>Ipsum dolor sit amet conse</li>
      </ul>
    </div>
    <div class="info-col info-locations">
      <h3>OUR LOCATIONS</h3>
      <div class="map-area" role="img" aria-label="Grey world map showing office locations"></div>
    </div>
  </section>

  <footer class="site-footer">© 2012 Halvern Marine. All Rights Reserved.</footer>
</body>
</html>
```